Snapnook needs You

Help us create an inviting, amazing, sleek, simple, clear landing page for a picture-memory-social connection site!

Business Name: SnapNook
Industry: Social Networking and Creativity through Pictures
A web platform for and about a community that is driven by a passion for sharing, caring, bonding, collaborating, creating and earning with pictures, through pictures and other related creative activities. This is going to be a great site for all creative artists-photographers, artists, graphic artists to express their work and their creativity.

The main focus of the site is - CONNECTIONS.
This will be uncoded.

Desired Website Screen Size
1024x768... Widescreen/Landscape orientation, is what we mean... So it fits on a CPU screen.

Desired look and feel and message
Look: Visitor should feel immersed in the page, in the world the page creates, simple, elegant, sophisticated, contemporary. We really like a clean uncluttered look.

Special mention: By the way we love the marketing genius who thought up this branding for velu yogurt where they used the two dots above the o to create a branding effect that made this brand instantly identifiable. http://www.velu-dairy.ca/en/

The two dots by themselves without having even the name present brings up the whole brand now. The dots are used above all the ingredients of the yogurt creating friendly figures, and above people in commercials-bringing the people onto the side of "team" velu. Snapnook may have a character created or something distinctive in the letters in the name created to brand the site as well.

Feel: Engaging; Magical without being corny, here is a link to give an example look and feel but please do not be hindered in your creativity by this suggestion. We love all creative angles.
http://artscrapyard.com/graphic/5829317-camera-film-roll-blue-background

Message: Life and memories and connections through pictures.

Target audience:
The site is focused on pictures but not confined to photography enthusiasts (although they are an integral part of the site). Customers/Visitors will include families, corporates and the younger generation - all age groups, all class, everyone with pictures to express, memories to share.

Website design we like:
http://brindlework.com/work/northern-ballet-house/
http://brindlework.com/work/zapverse/

What colors do we want to see on our landing page?
We would like the background to be grey or blue since it is grey is picture neutral colour and blue highlights pictures well and we also like blue and silver, which can be integrated into the theme. Also like green. But please do not let these instructions limit your creativity. We are open to new ideas and colours.

Predetermined Concepts if any:
We have a concept in mind and we think it would be cool to have an interface for the user through the back of a camera on the landing page -This could be used to create a scene or world the visitor feels a part of or is immersed into. The back screen of the camera may act as a screen for the slideshow of featured pictures on the site.

Content on the Page:
Photo Gallery with full screen, thumbnail view, zoom option etc.
Prominent but short introductory message
Sign in / Login Options
Links: Home Page; About; Info/Help; Contact Us; Privacy Policy; Terms of Use
At the bottom of the page: Follow Me/Like/Workplaza...social buttons.

Please feel free to add any other element to the landing page that you think might add to the effect of simple yet amazing look -clean, simple, uncluttered, sophisticated, stylish, inviting and engaging.
The concept is a guideline, but we would like you to be as creative as you can, even if it meant stepping out of these guidelines - rethink design, style, content if you like. We believe in bringing a solution in an innovative yet simple and elegant style. Something a visitor would be intrigued enough to explore and the guest would feel comfortable enough taking that step forward to have fun on the site. If you believe in the same, and you have the skill then you will have what we need. Good luck, go for it and we are excited to see what the amazing designers on this amazing site have to offer.
If you have any questions please free to ask.

HI wanted to send an update that this project design has been guaranteed.

Our site will be one to celebrate and showcase imagination as well as connection.  We would love to see what you create. Keep in mind our site will showcase all creativity, photographs, artists, graphic artists so this would be a benefit you may want to take advantage of in the future, a place where, if you so choose, you could gain exposure for your work. Therefore, even if you do not win the design project there is possible future benefit.

Imagination is everything.
Imagination encircles the world.-Halvorsen

Reason: We are giving the designers who accepted invites but have not yet submitted a chance to finish their submissions and the ones who are working on revisions a chance to finish those:)

Hello everyone,

Due to time constraints we must come to a decision sooner than the deadline of 28th. 

So, please try to submit any new designs or modifications to the old ones before the 26th. We are very thankful to all of you who have participated - for your designs, enthusiasm and kind words. 

Good luck! :)

• Thank you for the interest shown and your submissions! Designers who have submitted up until now have shown great potential. We are VERY excited with the quality of work and designs.

We want to add that Snapnook is not exclusively for the photographers. The site is for every person who may have a picture to store, organise, use or share - whether publicly or with only a few friends and family.

Snapnook is about allowing people to take control of their creativity. It is about providing tools to our users so that they can build their own connections and social network... of friends, family, fans, clients, ideas, thoughts, emotions etc. through pictures without worrying about their privacy or control over their creations.

With this update we want to encourage others to go beyond the camera theme. Do not let us restrict your creativity. Let YOUR OWN ideas take over if that’s what you think will best convey the message and will appeal to the users.

```html
<!DOCTYPE html>
<html lang="en">
<head>
<meta charset="utf-8">
<title>SnapNook</title>
<link href="https://fonts.googleapis.com/css2?family=Ubuntu:ital,wght@0,400;0,500;1,400&family=Ubuntu+Condensed&family=Roboto+Condensed:wght@400&display=swap" rel="stylesheet">
<style>
:root{
  --blue:#1fa3e0;
  --blue-deep:#0f86c4;
  --header:#222324;
  --stage:#1d1e1f;
  --body:#272829;
  --panel:#1f2021;
  --panel-line:#3a3b3c;
  --text:#ffffff;
  --muted:#e0e0e0;
  --soft:#9a9a9a;
  --footer:#1f2020;
  --cond:"Ubuntu Condensed","Roboto Condensed",sans-serif;
}
*{margin:0;padding:0;box-sizing:border-box}
html,body{width:1023px;height:1200px;overflow:hidden;background:var(--body)}
body{position:relative;font-family:"Ubuntu",sans-serif;color:var(--text)}
.abs{position:absolute}
.top-rule{left:0;top:0;width:1023px;height:4px;background:var(--blue)}
.site-header{left:0;top:4px;width:1023px;height:106px;background:var(--header)}
.brand-name{left:33px;top:52px;font-weight:400;font-size:42px;line-height:1;color:var(--text);letter-spacing:-0.5px}
.social{top:12px;left:806px;display:flex;gap:3px}
.social span{width:20px;height:20px;border-radius:50%;background:#8c8c8c}
.login{left:909px;top:0;width:66px;height:26px;background:linear-gradient(#2fb4ee,var(--blue-deep));border-radius:0 0 3px 3px;font-family:var(--cond);font-weight:400;font-size:15px;text-align:center;line-height:26px;color:#fff}
.main-nav{top:66px;right:61px;display:flex;align-items:center;font-family:var(--cond);font-weight:400;font-size:16px;color:#e6e6e6;white-space:nowrap}
.main-nav a{color:inherit;text-decoration:none}
.main-nav a.active{color:var(--blue)}
.main-nav .sep{width:1px;height:24px;background:#4a4a4a;transform:skewX(-25deg);margin:0 15px}
.header-rule{left:32px;top:107px;width:960px;height:1px;background:#3a3a3a}
.stage{left:0;top:110px;width:1023px;height:400px;background:var(--stage)}
.photo{position:absolute}
.feature{left:509px;top:265px;width:256px;height:172px;background:#fff;padding:7px;box-shadow:0 4px 14px rgba(0,0,0,.5)}
.feature div{width:100%;height:100%;background:linear-gradient(90deg,#dfe3e8 0%,#f4f4f2 35%,#e6e0d6 55%,#f0f1f3 75%,#d6dbe1)}
.slider-arrow{width:26px;height:26px;border-radius:50%;background:#333435;top:463px}
.wave{left:0;top:480px}
.intro{left:38px;top:550px;width:630px}
.intro h1{font-size:19px;font-weight:500;line-height:25px}
.intro p{font-size:11.5px;line-height:19px;color:var(--muted)}
.intro h1+p{margin-top:14px}
.intro p+p{margin-top:6px}
.section-title{font-family:var(--cond);font-weight:400;font-size:19px;color:#fff}
.gallery{left:39px;top:765px;width:613px;display:grid;grid-template-columns:repeat(7,1fr);gap:2px}
.gallery div{height:84px;border:2px solid #f2f2f2}
.upload{left:702px;top:544px;width:291px;height:149px;background:var(--panel);border:1px solid var(--panel-line)}
.upload h2,.blog h2{font-family:var(--cond);font-weight:400;font-size:19px}
.upload h2{position:absolute;left:23px;top:17px}
.upload p{position:absolute;left:23px;top:46px;font-size:11px;font-style:italic;color:#ddd}
.upload-field{left:20px;top:72px;width:236px;height:30px;background:#fff;border-radius:4px}
.upload-go{left:232px;top:67px;width:40px;height:40px;border-radius:50%;background:#2c2c2c;border:2px solid #3e3e3e;font-family:var(--cond);font-weight:400;font-size:18px;text-align:center;line-height:36px}
.blog{left:705px;top:698px;width:290px;height:422px;background:var(--panel);border:1px solid var(--panel-line)}
.blog h2{position:absolute;left:17px;top:16px}
.post{position:absolute;left:18px;width:260px;height:70px}
.post .thumb{position:absolute;left:0;top:0;width:64px;height:57px;border:2px solid #e8e8e8}
.post h3{position:absolute;left:77px;top:-3px;font-size:11.5px;font-weight:400;color:#eee;white-space:nowrap}
.post p{position:absolute;left:75px;top:14px;width:182px;font-size:10px;font-style:italic;line-height:16px;color:var(--soft)}
.more{right:18px;bottom:12px;font-family:var(--cond);font-weight:400;font-size:11px;color:#ddd}
.site-footer{left:0;top:1140px;width:1023px;height:60px;background:var(--footer)}
.site-footer p{position:absolute;left:38px;top:20px;font-size:10.5px;color:#9b9b9b}
</style>
</head>
<body>
<div class="abs top-rule"></div>
<header class="abs site-header">
  <span class="abs brand-name">SnapNook</span>
  <div class="abs social"><span></span><span></span><span></span><span></span></div>
  <div class="abs login">Login</div>
  <nav class="abs main-nav">
    <a class="active" href="#">Home</a><span class="sep"></span>
    <a href="#">About</a><span class="sep"></span>
    <a href="#">Help</a><span class="sep"></span>
    <a href="#">Contact Us</a><span class="sep"></span>
    <a href="#">Privacy Policy</a><span class="sep"></span>
    <a href="#">Terms of Use</a>
  </nav>
  <div class="abs header-rule"></div>
</header>

<section class="abs stage"></section>
<div class="abs photo" style="left:34px;top:141px;width:238px;height:139px;background:linear-gradient(100deg,#f6f8ff 0%,#9aa6d8 30%,#3b4180 60%,#12173a)" role="img" aria-label="City skyline at night with light trails"></div>
<div class="abs photo" style="left:276px;top:141px;width:239px;height:139px;background:linear-gradient(#f1ead2 0%,#b8b08a 30%,#6c6a3a 55%,#3f3d22)" role="img" aria-label="White car on a country road"></div>
<div class="abs photo" style="left:521px;top:141px;width:230px;height:124px;background:linear-gradient(#4f7fa8,#9fbdd6 55%,#c9d7e2 75%,#9a7a58)" role="img" aria-label="Models posing against a blue sky"></div>
<div class="abs photo" style="left:755px;top:141px;width:230px;height:139px;background:linear-gradient(#d6ecf6,#a9cbd8 35%,#3d5e22 55%,#86b43e)" role="img" aria-label="Golfer on a green course"></div>
<div class="abs photo" style="left:34px;top:283px;width:238px;height:138px;background:linear-gradient(100deg,#1c1c1c,#4a4a4a 35%,#a6a6a6 65%,#eeeeee)" role="img" aria-label="Car interior dashboard"></div>
<div class="abs photo" style="left:276px;top:283px;width:233px;height:138px;background:linear-gradient(#fbfaf4,#dcdac6 40%,#9a9678 70%,#b8b6a4)" role="img" aria-label="Silver car beside trees"></div>
<div class="abs photo" style="left:765px;top:283px;width:220px;height:138px;background:linear-gradient(90deg,#6e5442,#c9a88e 45%,#e8d8c8 70%,#f2f3f6)" role="img" aria-label="Portrait of a man"></div>
<div class="abs feature"><div role="img" aria-label="Featured portrait in front of a city skyline"></div></div>
<div class="abs slider-arrow" style="left:484px"></div>
<div class="abs slider-arrow" style="left:523px"></div>
<svg class="abs wave" width="1023" height="40" viewBox="0 0 1023 40" aria-hidden="true">
  <path d="M0 8 Q480 36 1023 20 L1023 40 L0 40 Z" fill="var(--body)"/>
  <path d="M0 8 Q480 36 1023 20" fill="none" stroke="var(--blue)" stroke-width="4"/>
</svg>

<section class="abs intro">
  <h1>Imagination is everything.<br>Imagination encircles the world.- Albert Halvorsen</h1>
  <p>Pellentesque habitant morbi tristique senectus et netus et malesuada fames ac turpis egestas. In posuere felis nec tortor. Pellentesque faucibus. Ut accumsan ultricies elit. Maecenas at justo id velit placerat molestie.</p>
  <p>Donec dictum lectus non odio. Cras a ante vitae enim iaculis aliquam. Mauris nunc quam, venenatis nec, euismod sit amet, egestas placerat, est. Pellentesque habitant morbi tristique senectus et netus et malesuada fames ac turpis egestas.</p>
</section>

<h2 class="abs section-title" style="left:41px;top:732px">Best Viewed Photos</h2>
<div class="abs gallery" role="img" aria-label="Grid of most viewed photos: flowers, candles, grasses and textures">
  <div style="background:radial-gradient(circle,#e25aa8,#a82a70)"></div><div style="background:radial-gradient(circle,#a070b0,#6a5040)"></div><div style="background:linear-gradient(#a89478,#5e4e38)"></div><div style="background:linear-gradient(135deg,#e0e4e8,#50565c)"></div><div style="background:radial-gradient(circle,#e03a2a,#3a60b0)"></div><div style="background:radial-gradient(circle,#f08a2a,#b84a10)"></div><div style="background:linear-gradient(#7080a8,#4e5a3a)"></div>
  <div style="background:linear-gradient(#c0a870,#7a6038)"></div><div style="background:linear-gradient(#a8c4dc,#2e3a4a)"></div><div style="background:radial-gradient(circle,#f48040,#d04a10)"></div><div style="background:linear-gradient(#b8bcc4,#8a7a4a)"></div><div style="background:linear-gradient(#e8ecea,#3a5a2a)"></div><div style="background:radial-gradient(circle,#d86a3a,#4a6a3a)"></div><div style="background:radial-gradient(circle,#e88a2a,#1a140e 70%)"></div>
  <div style="background:linear-gradient(#8aa06a,#4e5a30)"></div><div style="background:radial-gradient(circle,#e870b0,#4a6a30)"></div><div style="background:linear-gradient(#9a8a70,#4a3a28)"></div><div style="background:linear-gradient(#a8a488,#6a6a42)"></div><div style="background:linear-gradient(#6a6a6a,#3a3630)"></div><div style="background:linear-gradient(#c8d0c4,#6a7a3a)"></div><div style="background:linear-gradient(90deg,#bababa,#5a5a5a)"></div>
  <div style="background:radial-gradient(circle,#e8902a,#100c08 65%)"></div><div style="background:linear-gradient(#5e7a4a,#3a4a2a)"></div><div style="background:radial-gradient(circle,#d07a2a,#141210 60%)"></div><div style="background:radial-gradient(circle at 50% 40%,#5ac8d8,#0e2a3a 70%)"></div><div style="background:linear-gradient(120deg,#2a4a1a,#8ab83a,#3a6a1a)"></div><div style="background:linear-gradient(90deg,#4a3a28,#c8b498,#5a4a38)"></div><div style="background:linear-gradient(#8a8e92,#4e5256)"></div>
</div>

<aside class="abs upload">
  <h2>Upload your Photo</h2>
  <p>Nam eget lacus. Aliquam erat volutpat.</p>
  <div class="abs upload-field"></div>
  <div class="abs upload-go">Go</div>
</aside>

<aside class="abs blog">
  <h2>Photos Blog &amp; Comments</h2>
  <article class="post" style="top:57px"><div class="thumb" style="background:linear-gradient(#8ab06a,#2e4a22)" role="img" aria-label="Green tree canopy"></div><h3>Etiam est nunc</h3><p>Pellentesque habitant morbi tristique senectus et netus et malesuada fames ac turpis egestas. In posuere felis nec</p></article>
  <article class="post" style="top:139px"><div class="thumb" style="background:linear-gradient(120deg,#6a6a62,#f2f2ee 55%,#9a9a90)" role="img" aria-label="White flower close-up"></div><h3>Nam eget lacus.</h3><p>Pellentesque habitant morbi tristique senectus et netus et malesuada fames ac turpis egestas. In posuere felis nec</p></article>
  <article class="post" style="top:219px"><div class="thumb" style="background:radial-gradient(circle,#7ac04a,#2e5a1e)" role="img" aria-label="Green leaves"></div><h3>Phasellus pellentesque aliquam</h3><p>Pellentesque habitant morbi tristique senectus et netus et malesuada fames ac turpis egestas. In posuere felis nec</p></article>
  <article class="post" style="top:305px"><div class="thumb" style="background:linear-gradient(#6a8ac8,#3a5a9a)" role="img" aria-label="Red flowers against blue sky"></div><h3>Ut velit enim</h3><p>Pellentesque habitant morbi tristique senectus et netus et malesuada fames ac turpis egestas. In posuere felis nec</p></article>
  <div class="abs more">VIEW MORE BLOG ▸</div>
</aside>

<footer class="abs site-footer"><p>© 2012 Company Name.&nbsp; All right reserved.&nbsp; Term of Use</p></footer>
</body>
</html>
```